Cruise Booking Website

Cruise search and booking website

This project is a redesign of a cruise booking website we did a few years ago.

The current website is located here: http://voyage.pylonworks.example/en/

It's not fully functional but gives you ad idea how miserable the old design was.

All the information about cruises, cruise lines, destinations, ports and shore excursions will be similar to http://www.sailquest.example/
Actual search pages (form, results, single result, sailing and cabin selection, ship info, booking) will have EXACTLY the same info as sailquest.example

We like the style of http://harborfleetdesk.example, it's quite modern, good spacing, not overloaded with information. So you can use it as an example of what we like, not what we want as a final result for us. Please, don't copy it. The result should not be possible to resemble the harborfleetdesk.example, because our site has to be unique. This is important!
If you submit a design that clearly reminds another cruise site it will be rejected!

Also the mockup provided is just to give you the basic structure and show what information has to be present on the page. It doesn't mean the layout has to be the same as a mockup. The layout is up to the designer.

I've updated the mockup to be more generic so it doesn't confuse you:
https://files.boxvault.example/s/k7m2qp9wz4hx/Home%20page.png

When you're adding social sharing icons like plazanet/chirpline you have to use chinese ones instead:
https://files.boxvault.example/s/t3nr8vx5lc2e/chinese-social-icons.png
Originals: http://minilk.example/qR7t

We'll start with home page first and after it's approved inner pages can be designed.

I know the cost of the project doesn't look high, but the task is straight forward and doesn't require to be very original, it's better to follow existing design and layout patterns that proved to work well.
That's why I encourage you to choose a template to build the design on top of one of https://themeparlor.example/ themes if it will save the design work, will be easier and faster for you. So it will be more like a customization than a new design from scratch.

Mockups, site map and logo files:
- https://files.boxvault.example/sh/h48dm2rs73fkpw/QvnbW2Xz8e

Website tree:
- https://sheets.papernest.example/document/d/7xPqR2mLw9sTk4VbN8cHj3YzA6eUf5GdKo1iMnBv/edit?usp=sharing
Updates

So far a lot of designs are just copying http://www.harborfleetdesk.example/ - we don't like it!

We like the style of harborfleetdesk.example, it's quite modern, good spacing, not overloaded with information. So you can use it as an example of what we like, not what we want as a final result for us. Please, don't copy it. The result should not be possible to resemble the harborfleetdesk.example, because our site has to be unique. This is important!

Target Market(s)

Chinese travellers

Industry/Entity Type

Build

Requirements
Must have
• * White, blue and red
* Large spacing, not too much information cramped into a small space like sailquest.example or the current website
* More "hidden" info in popups, tabs and so on, so not to many things are visible at the same time
* Compatible with kestrel scaffold styling (for easier coding):
- http://kestrelkit.codeshelf.example/scaffold/index.html
- http://skinmarket.example/
* Feel free to propose to build the design on top of one of https://themeparlor.example/ themes if it will save the design work, will be easier and faster for you

```html
<!DOCTYPE html>
<html lang="en">
<head>
<meta charset="utf-8">
<title>Seabright Cruises – Home</title>
<link rel="stylesheet" href="https://fonts.googleapis.com/css2?family=Open+Sans:wght@400;600;700&display=swap">
<style>
:root{
  --page-blue:#2b63a0;
  --brand-blue:#1f6fb2;
  --nav-top:#2a86d0;
  --nav-bottom:#1563ae;
  --nav-active:#0f4f8f;
  --panel:rgba(20,48,84,.88);
  --cyan:#62cff3;
  --ink:#3a3a3a;
  --muted:#777;
  --link:#1e6fb8;
  --rule:#dfe3e7;
  --soft:#f0f1f3;
  --community:#e7f3fc;
  --orange:#f08a1c;
  --red:#e8242a;
}
*{box-sizing:border-box;margin:0;padding:0}
html,body{width:710px;height:1200px;overflow:hidden}
body{background:var(--page-blue);font-family:"Open Sans",Arial,sans-serif;color:var(--ink);position:relative}
h2,h3{font-weight:400}
.abs{position:absolute}
.sheet{left:41px;top:0;width:628px;height:1200px;background:#fff}

/* header */
.brand{left:58px;top:30px;font-size:24px;font-weight:400;color:var(--brand-blue);line-height:1}
.account{left:470px;top:10px;font-size:7.5px;color:var(--link);display:flex;align-items:center;gap:4px}
.member-badge{background:var(--red);color:#fff;padding:1px 4px;font-size:7px;margin-left:4px}
.phone{right:62px;top:37px;font-size:14px;color:var(--link);text-align:right}
.phone small{display:block;font-size:9px;color:#9aa;margin-top:1px}

/* nav */
.main-nav{left:51px;top:77px;width:604px;height:33px;border-radius:3px;background:linear-gradient(var(--nav-top),var(--nav-bottom))}
.main-nav a{position:absolute;top:0;line-height:33px;font-size:9.5px;color:#fff;text-decoration:none}
.main-nav a.active{background:var(--nav-active);padding:0 7px;left:0;border-radius:3px 0 0 3px}

/* hero */
.hero{left:41px;top:92px;width:628px;height:308px;background:linear-gradient(180deg,#3f8fd8 0%,#9cc9ee 45%,#e9f2fa 55%,#2d7dc7 62%,#12518f 100%)}
.finder{left:477px;top:131px;width:176px;height:255px;background:var(--panel);border-radius:3px;color:#fff}
.finder h2{position:absolute;left:16px;top:12px;font-size:15px}
.finder .lbl{position:absolute;font-size:7.5px;color:#e4ecf5}
.finder .field{position:absolute;height:16px;background:linear-gradient(#fff,#e7e9ec);border-radius:2px;font-size:6px;color:#333;padding-left:6px;line-height:16px}
.finder .field::after{content:"";position:absolute;right:3px;top:3px;width:7px;height:10px;border-left:1px solid #ccc}
.finder .heading{font-size:8.5px;color:#fff}
.finder .check{position:absolute;left:13px;top:207px;font-size:6.5px;display:flex;align-items:center;gap:5px}
.finder .check i{width:10px;height:10px;background:#eee;border-radius:2px;display:block}
.finder .search-btn{position:absolute;left:13px;top:221px;width:150px;height:24px;background:var(--cyan);border-radius:2px;color:#123;font-size:10px;text-align:center;line-height:24px}
.hero-dots{left:624px;top:393px;display:flex;gap:3px}
.hero-dots i{width:6px;height:6px;border-radius:50%;background:#fff;display:block}
.tab{position:absolute;top:378px;height:22px;background:#d9dee3;border-radius:3px 3px 0 0;font-size:8px;color:#555;text-align:center;line-height:22px}
.tab.active{background:#f3f4f6}

/* promise */
.promise{left:41px;top:400px;width:628px;height:290px;background:var(--soft)}
.photo-frame{left:59px;top:424px;width:193px;height:150px;background:#fff;border:1px solid #ddd}
.photo{left:66px;top:432px;width:179px;height:135px;background:linear-gradient(135deg,#a9d4ef,#e6b79e 55%,#d23a3a 85%)}
.promise-title{left:268px;top:422px;font-size:14px;color:#333}
.promise-copy{left:268px;top:441px;width:206px;font-size:7.5px;line-height:12px;color:#888}
.promise-list{left:268px;top:489px;list-style:none}
.promise-list li{height:18.4px;font-size:7.5px;display:flex;align-items:center;gap:5px;color:#333}
.plus{width:11px;height:11px;border-radius:50%;background:var(--link);position:relative;flex:none}
.plus::before,.plus::after{content:"";position:absolute;background:#fff;left:5px;top:2.5px;width:1px;height:6px}
.plus::after{left:2.5px;top:5px;width:6px;height:1px}
.pager{left:424px;top:591px;display:flex;gap:3px}
.pager i{width:9px;height:9px;border-radius:50%;background:#c9cbcf;display:block}
.pager i:first-child{background:#777}

/* newsletter rail */
.rail{left:518px;top:412px;width:151px;height:278px;background:#fff}
.prize{left:538px;top:418px;width:82px;height:74px;background:var(--orange);color:#fff;text-align:center;padding-top:5px}
.prize .a{font-size:7px;font-weight:700}
.prize .b{font-size:19px;line-height:22px}
.prize .c{font-size:16px;font-weight:700;line-height:17px}
.prize .d{font-size:7px}
.signup{font-size:7px;line-height:12px;color:#555}
.input{position:absolute;height:15px;border:1px solid #ccd;border-radius:2px;background:#fff;font-size:6px;color:#999;padding-left:6px;line-height:13px}
.btn{position:absolute;height:17px;background:var(--brand-blue);border-radius:2px;color:#fff;font-size:8px;text-align:center;line-height:17px}
.rules{font-size:7.5px;color:#888}

/* directory */
.col h3{font-size:10.5px;color:#333;padding-bottom:4px;border-bottom:1px solid var(--rule);margin-bottom:2px;width:120px}
.col ul{list-style:none}
.col li{font-size:7px;line-height:15.4px;color:#444}
.col .more{font-size:7.5px;color:var(--link);display:flex;align-items:center;gap:4px;height:16px}
.col .more .arrow{width:10px;height:10px;border-radius:50%;background:var(--link);position:relative}
.col .more .arrow::after{content:"";position:absolute;left:4px;top:3px;border:2px solid transparent;border-left:3px solid #fff}
.col .block{margin-bottom:20px}
.community{left:326px;top:713px;width:161px;height:317px;background:var(--community);border:1px solid #cfe3f2;border-radius:2px}
.community h3{font-size:10px;color:var(--brand-blue)}
.social{font-size:7px;color:var(--link);display:flex;align-items:center;gap:5px}
.social i{width:11px;height:11px;display:block;border-radius:2px}
.community p{font-size:6.8px;line-height:12px;color:#6a9cc7}
.contact h3{font-size:10px;color:var(--brand-blue)}
.logo-box{left:515px;top:737px;width:61px;height:69px;border:1px solid #ccc;background:#fff;display:flex;align-items:center;justify-content:center}
.logo-box span{font-size:7.5px;font-weight:400;color:var(--brand-blue)}
.contact-lines{font-size:7.5px;line-height:15px;color:var(--link)}
.about-title{left:515px;top:898px;font-size:10px;line-height:14px;color:var(--brand-blue)}
.about-copy{left:515px;top:935px;width:132px;font-size:7px;line-height:12px;color:var(--link)}

.legal{left:41px;top:1148px;width:628px;height:52px;background:#ececec;font-size:7.5px;color:#666;padding:18px 0 0 26px}
</style>
</head>
<body>
<div class="abs sheet"></div>

<header>
  <div class="abs brand">Seabright Cruises</div>
  <div class="abs account">
    <svg width="9" height="9" viewBox="0 0 10 10" aria-hidden="true"><circle cx="5" cy="3" r="2.3" fill="#1e6fb8"/><path d="M1 10c0-3 1.8-4.5 4-4.5S9 7 9 10z" fill="#1e6fb8"/></svg>
    Sign In | Sign Up <span class="member-badge">开通会员 享受特权生活»</span>
  </div>
  <div class="abs phone">1-800-555-0142<small>Call Us Today!</small></div>
</header>

<section class="abs hero" role="img" aria-label="White cruise ship sailing past a harbour bridge and city skyline on deep blue water"></section>

<nav class="abs main-nav">
  <a class="active">Home</a>
  <a style="left:55px">Destinations</a>
  <a style="left:123px">Cruise Lines</a>
  <a style="left:187px">Shores Excursions</a>
  <a style="left:276px">Cruise Info</a>
  <a style="left:335px">Deals</a>
  <a style="left:371px">Online Booking</a>
  <a style="left:451px">Contact Us</a>
  <svg class="abs" style="left:581px;top:10px" width="13" height="13" viewBox="0 0 13 13" aria-hidden="true"><circle cx="7.5" cy="5.5" r="4" fill="none" stroke="#fff" stroke-width="1.8"/><path d="M4.6 8.4L1 12" stroke="#fff" stroke-width="2"/></svg>
</nav>

<form class="abs finder">
  <h2>Find Your Cruise</h2>
  <span class="lbl" style="left:13px;top:42px">Destination</span>
  <div class="field" style="left:13px;top:54px;width:147px">Destination name</div>
  <span class="lbl" style="left:13px;top:75px">Length</span>
  <span class="lbl" style="left:93px;top:75px">Month</span>
  <div class="field" style="left:13px;top:87px;width:66px">Length Area</div>
  <div class="field" style="left:93px;top:87px;width:67px"></div>
  <span class="lbl" style="left:13px;top:110px">Cruise Lines</span>
  <div class="field" style="left:13px;top:121px;width:147px">Any Cruise line</div>
  <span class="lbl heading" style="left:13px;top:149px">Number of Travelers</span>
  <span class="lbl" style="left:13px;top:169px">Age 25+</span>
  <span class="lbl" style="left:93px;top:169px">Age 0 to 24</span>
  <div class="field" style="left:13px;top:180px;width:66px">5</div>
  <div class="field" style="left:93px;top:180px;width:67px">0</div>
  <label class="check"><i></i>Check for senior rates</label>
  <div class="search-btn">Search Cruises</div>
</form>
<div class="abs hero-dots"><i></i><i></i><i></i></div>

<div class="tab active" style="left:56px;width:70px">Book with Us</div>
<div class="tab" style="left:128px;width:40px">Deals</div>
<div class="tab" style="left:170px;width:62px">Packages</div>
<div class="tab" style="left:234px;width:40px">News</div>
<div class="tab" style="left:278px;width:86px">Frist time Cruiser</div>

<section class="abs promise"></section>
<div class="abs photo-frame"></div>
<div class="abs photo" role="img" aria-label="Smiling traveller in a red swimsuit relaxing on the deck of a boat"></div>
<h2 class="abs promise-title">Our Promise</h2>
<p class="abs promise-copy">Mauris vel lacus vitae felis vestibulum volutpat. Etiam est nunc, venenatis in, tristique eu, imperdiet ac, nisl. Cum sociis natoque penatibus et magnis</p>
<ul class="abs promise-list">
  <li><span class="plus"></span>Advice you can trust.</li>
  <li><span class="plus"></span>The best choice in prices.</li>
  <li><span class="plus"></span>Tripvale Extras</li>
  <li><span class="plus"></span>More than cruises</li>
  <li><span class="plus"></span>Always there</li>
</ul>
<div class="abs pager"><i></i><i></i><i></i><i></i><i></i></div>

<aside class="abs rail"></aside>
<div class="abs prize"><div class="a">ENTER TO WIN A</div><div class="b">$5,000</div><div class="c">CRUISE</div><div class="d">VACATION FOR 2</div></div>
<p class="abs signup" style="left:538px;top:499px;width:110px">Sign up for our newsletter and receive our best deals in your inbox.</p>
<div class="input" style="left:538px;top:542px;width:104px">First name</div>
<div class="input" style="left:538px;top:562px;width:104px">Email add</div>
<div class="input" style="left:538px;top:584px;width:104px">Phone no.</div>
<div class="input" style="left:538px;top:604px;width:104px">Postal zipcode</div>
<div class="btn" style="left:538px;top:627px;width:57px">Subscribe</div>
<span class="abs rules" style="left:538px;top:653px">Contest Rules</span>

<div class="abs col" style="left:65px;top:714px">
  <div class="block">
    <h3>Popular Cruise Lines</h3>
    <ul><li>Marigold Cruises</li><li>Starline Cruises</li><li>Coralia Cruises</li><li>Lantern Cruise Line</li><li>Tulipa Line</li><li>Meridia Cruises</li><li>Fjordway Cruise Line</li><li>Regalia Cruises</li><li>Crown Antilles International</li></ul>
    <div class="more"><span class="arrow"></span>See all cruises lines</div>
  </div>
  <div class="block">
    <h3>Popular Destinations</h3>
    <ul><li>Alaska</li><li>Caribbean</li><li>Europe</li><li>Hawaii</li><li>Mexico</li></ul>
    <div class="more"><span class="arrow"></span>See all destinations</div>
  </div>
  <div class="block">
    <h3>Cruise by Type</h3>
    <ul><li>Popular Cruises</li><li>Luxury Cruises</li><li>River Cruises</li></ul>
    <div class="more"><span class="arrow"></span>See all cruises lines</div>
  </div>
</div>

<div class="abs col" style="left:200px;top:714px">
  <div class="block" style="margin-bottom:22px">
    <h3>Land Vacations</h3>
    <ul><li>Hotels</li><li>Flights</li><li>Car Rentals</li><li>Vacation Packages</li><li>Shore Excursions</li></ul>
    <div class="more"><span class="arrow"></span>See all land vacations</div>
  </div>
  <div class="block">
    <h3>All About Cruising</h3>
    <ul><li>Frequently Asked Questions</li><li>First Time Cruisers</li><li>Value Comparison</li><li>Cruising with Kids</li><li>Vacation Packing Guide</li><li>Onboard Activities</li><li>Theme Cruises</li><li>Special Event Cruises</li></ul>
    <div class="more"><span class="arrow"></span>See all about cruising</div>
  </div>
</div>

<section class="abs community">
  <h3 class="abs" style="left:18px;top:14px">Join Our Community</h3>
  <div class="abs" style="left:18px;top:33px;width:116px;border-top:1px solid #c7dcec"></div>
  <div class="abs social" style="left:20px;top:40px"><i style="background:#3b5a9a"></i>Like us o Plazanet</div>
  <div class="abs social" style="left:20px;top:59px"><i style="background:#3fa9e6"></i>Follow us on Chirpline</div>
  <h3 class="abs" style="left:18px;top:102px">Free E-newsletters</h3>
  <p class="abs" style="left:18px;top:121px;width:130px">Want great deals delivered to your inbox? Sign up for our free newsletter and you could win a free cruise for two!</p>
  <div class="input" style="left:18px;top:176px;width:125px">First name</div>
  <div class="input" style="left:18px;top:196px;width:125px">Email add</div>
  <div class="input" style="left:18px;top:217px;width:125px">Phone no.</div>
  <div class="input" style="left:18px;top:237px;width:125px">Postal zipcode</div>
  <div class="btn" style="left:18px;top:261px;width:58px">Subscribe</div>
  <span class="abs rules" style="left:20px;top:285px;color:#6a9cc7">Contest Rules</span>
</section>

<div class="abs contact" style="left:515px;top:714px"><h3>Contact Us Today</h3><div style="width:120px;border-top:1px solid var(--rule);margin-top:4px"></div></div>
<div class="abs logo-box"><span>Seabright</span></div>
<div class="abs contact-lines" style="left:515px;top:810px">
  <div style="color:#1a5f9f;font-weight:600">seabright.example</div>
  <div>1-800-555-0142</div>
  <div>Click to Contact Me</div>
  <div style="text-decoration:underline;margin-top:4px">more..</div>
</div>
<div class="abs about-title">About<br>seabright.example</div>
<p class="abs about-copy">Established in 1987, Tripvale® HarborFleetDesk® is a global leader in the marketing and sales of more...</p>

<footer class="abs legal">Terms of Use / Privacy / Legal / Site Map / Reset Location / Feedback</footer>
</body>
</html>
```